Business Card for premium dental clinic

We are a premium dental clinic based in Brasov, Romania with more than 15 year on the market, providing quality dental treatment made by a team of more specialized dentists, working with modern equipment as a solution to beautiful and healthy teeth.

Our current logo for the clinic use 2 square with colors black and gold - dr Ternisu - studio, using family fonts Bodoni, Myriad Pro and Segoe Print.
Depending on the printing we used some gold CMYK background or gold foil picture background or a gold gradient.
We want a business card:
- eye catching business card
- distinguished business card
- premium design
- to keep the color scheme of black and gold
- to attract the customers to spent time reading the information
- modern concept

```html
<!DOCTYPE html>
<html lang="en">
<head>
<meta charset="utf-8">
<title>dr Ternisu studio – Business Card</title>
<link href="https://fonts.googleapis.com/css2?family=Montserrat:wght@400;500&display=swap" rel="stylesheet">
<style>
  :root {
    --backdrop: #2e2724;
    --card-black: #1d1d1d;
    --card-white: #ffffff;
    --gold: #f2d04a;
    --gold-deep: #d9a91e;
    --ink: #1a1a1a;
    --grey: #7d7d7d;
    --paper-edge: #c9b23a;
  }
  * { margin: 0; padding: 0; box-sizing: border-box; }
  html, body {
    width: 1200px; height: 716px; overflow: hidden;
    background: var(--backdrop);
    font-family: "Montserrat", sans-serif;
  }
  .stage { position: relative; width: 1200px; height: 716px; }

  .card {
    position: absolute;
    width: 540px; height: 308px;
    border-radius: 4px;
    box-shadow: 0 14px 30px rgba(0,0,0,.45);
  }

  /* Front */
  .card-front {
    left: 40px; top: 204px;
    background: var(--card-black);
    border-bottom: 4px solid var(--paper-edge);
    display: flex; align-items: center; justify-content: center;
  }

  .brand {
    display: flex; align-items: center; gap: 14px;
    font-family: "Montserrat", sans-serif;
    font-weight: 500;
    letter-spacing: .02em;
  }
  .brand-square {
    width: 56px; height: 56px;
    background: linear-gradient(135deg, var(--gold) 0%, var(--gold-deep) 100%);
  }
  .card-front .brand-name { color: #ffffff; font-size: 24px; }

  /* Back */
  .card-back {
    left: 620px; top: 204px;
    background: var(--card-white);
  }
  .card-back .brand {
    position: absolute; right: 34px; top: 40px;
  }
  .card-back .brand-square { width: 48px; height: 48px; }
  .card-back .brand-name { color: var(--ink); font-size: 19px; }

  .holder-name {
    position: absolute; left: 34px; top: 122px;
    color: var(--gold);
    font-size: 24px; font-weight: 400;
    letter-spacing: .04em;
  }
  .name-rule {
    position: absolute; left: 196px; right: 34px; top: 140px;
    height: 1.5px; background: var(--gold);
  }

  .contact {
    position: absolute; left: 34px; top: 164px;
    list-style: none;
    color: var(--grey);
    font-size: 12.5px; line-height: 20px;
  }
  .contact li { display: flex; align-items: center; gap: 8px; }
  .contact svg { width: 10px; height: 10px; flex: none; }
  .contact .address { padding-left: 0; margin-top: 2px; }
</style>
</head>
<body>
<main class="stage">

  <section class="card card-front" aria-label="Card front">
    <div class="brand">
      <span class="brand-square"></span>
      <span class="brand-name">dr Ternisu studio</span>
    </div>
  </section>

  <section class="card card-back" aria-label="Card back">
    <div class="brand">
      <span class="brand-square"></span>
      <span class="brand-name">dr Ternisu studio</span>
    </div>

    <h1 class="holder-name">DR TERNISU</h1>
    <div class="name-rule"></div>

    <ul class="contact">
      <li>
        <svg viewBox="0 0 10 10" aria-hidden="true"><path d="M2 1 L4 1 L4.6 3 L3.4 4 Q4.5 6 6 6.6 L7 5.4 L9 6 L9 8 Q5 9 1 3 Z" fill="var(--gold)"/></svg>
        +40 268 555 019
      </li>
      <li>
        <svg viewBox="0 0 10 10" aria-hidden="true"><rect x="0.7" y="2" width="8.6" height="6" fill="none" stroke="var(--gold)" stroke-width="1"/><path d="M0.7 2 L5 5.4 L9.3 2" fill="none" stroke="var(--gold)" stroke-width="1"/></svg>
        info@drternisu.ro
      </li>
      <li>
        <svg viewBox="0 0 10 10" aria-hidden="true"><circle cx="5" cy="5" r="4" fill="none" stroke="var(--gold)" stroke-width="1"/><path d="M1 5 H9 M5 1 Q2.5 5 5 9 M5 1 Q7.5 5 5 9" fill="none" stroke="var(--gold)" stroke-width=".8"/></svg>
        www.drternisu.ro
      </li>
      <li class="address">Strada Lungă 48,</li>
      <li class="address">Brașov 500058, Romania</li>
    </ul>
  </section>

</main>
</body>
</html>
```